Venture 482 - Lumora Book Cover

I am looking for a Lumora book cover for my book about "Venture 482".
The Book is Titled:
Venture 482 Ascended
Shaping Outcomes: Paths To Unlocking Cosmic Truths
Author is Dorian Pell
Here is a book description that may help you understand more about it:
Inspired by the genius of Edwin Marlowe, this comprehensive guide delves into the ancient wisdom and cutting-edge science behind the 482 method, a powerful tool for manifesting your desires. Whether you're seeking personal growth, financial success, or spiritual enlightenment, this book provides advanced techniques and methods to transform your dreams into reality.
Any questions please ask.
Thanks
Owen

```html
<!DOCTYPE html>
<html lang="en">
<head>
<meta charset="utf-8">
<title>Venture 482 Ascended — Dorian Pell</title>
<link rel="stylesheet" href="https://fonts.googleapis.com/css2?family=Anton&family=Bebas+Neue&family=Oswald:wght@200;300&display=swap">
<style>
  :root {
    --red-core: #e3182c;
    --red-mid: #c3172a;
    --red-deep: #8f1522;
    --red-edge: #5c1019;
    --ink-white: #fbf7f5;
    --accent-amber: #f2a20c;
    --glyph-silver: #c9ccd2;
  }
  * { margin: 0; padding: 0; box-sizing: border-box; }
  html, body { width: 805px; height: 1200px; overflow: hidden; }
  body { background: var(--red-edge); }

  .cover {
    position: relative;
    width: 805px;
    height: 1200px;
    overflow: hidden;
    background: radial-gradient(circle at 400px 560px,
      var(--red-core) 0 120px,
      #dc172b 120px 210px,
      #d1172a 210px 300px,
      var(--red-mid) 300px 385px,
      #b31628 385px 465px,
      #a11524 465px 545px,
      var(--red-deep) 545px 625px,
      #7b1320 625px 705px,
      #6a111c 705px 790px,
      var(--red-edge) 790px);
    color: var(--ink-white);
  }

  .sigil {
    position: absolute;
    left: 425px;
    top: 226px;
    width: 270px;
    height: 275px;
    border-radius: 50%;
    background: radial-gradient(circle, rgba(201,204,210,0.35) 0 30%, rgba(201,204,210,0.12) 60%, rgba(201,204,210,0) 72%);
  }

  .title { font-weight: 400; }

  .series-word {
    position: absolute;
    left: 191px;
    top: 203px;
    font-family: "Bebas Neue", sans-serif;
    font-size: 122px;
    line-height: 1;
    transform: scaleX(0.83);
    transform-origin: left top;
  }

  .series-number {
    position: absolute;
    left: 0;
    width: 805px;
    top: 306px;
    text-align: center;
    font-family: "Anton", sans-serif;
    font-size: 311px;
    line-height: 1;
    transform: scaleX(0.91);
    text-shadow: 6px 10px 18px rgba(60, 0, 10, 0.45);
  }

  .series-edition {
    position: absolute;
    left: 197px;
    width: 436px;
    top: 623px;
    font-family: "Bebas Neue", sans-serif;
    font-size: 98px;
    line-height: 1;
    display: flex;
    justify-content: space-between;
  }

  .subtitle {
    position: absolute;
    left: 0;
    width: 805px;
    text-align: center;
  }
  .subtitle-lead {
    top: 793px;
    font-family: "Bebas Neue", sans-serif;
    font-size: 74px;
    line-height: 1;
    letter-spacing: 1px;
  }
  .subtitle-line {
    font-family: "Oswald", sans-serif;
    font-weight: 200;
    font-size: 50px;
    line-height: 1;
    color: var(--accent-amber);
    letter-spacing: -0.5px;
  }
  .subtitle-line.first { top: 870px; }
  .subtitle-line.second { top: 939px; }

  .author {
    position: absolute;
    left: 69px;
    width: 669px;
    top: 1058px;
    font-family: "Bebas Neue", sans-serif;
    font-size: 122px;
    line-height: 1;
    display: flex;
    justify-content: space-between;
  }
</style>
</head>
<body>
  <main class="cover">
    <div class="sigil" role="img" aria-label="Silver sacred geometry sigil of circles, triangles and radiating lines"></div>

    <h1 class="title">
      <span class="series-word">VENTURE</span>
      <span class="series-number">482</span>
      <span class="series-edition"><span>A</span><span>S</span><span>C</span><span>E</span><span>N</span><span>D</span><span>E</span><span>D</span></span>
    </h1>

    <p class="subtitle subtitle-lead">SHAPING OUTCOMES:</p>
    <p class="subtitle subtitle-line first">PATHS TO UNLOCKING</p>
    <p class="subtitle subtitle-line second">COSMIC TRUTHS</p>

    <p class="author"><span>D</span><span>O</span><span>R</span><span>I</span><span>A</span><span>N</span><span>&nbsp;</span><span>P</span><span>E</span><span>L</span><span>L</span></p>
  </main>
</body>
</html>
```